New Business Card for Software Company

We are looking at rebranding a 10 year old company that specializes in PDF and DWF solutions for Architects and Engineers. We will attach the new company logo that we are going with so you can work with that and complimentary colors.
The sample information we would like on the business card is:
Gerald Pinfold
Vice President
4738 W. Harrowgate Lane. STE 305
PMB#417
Larkmoor, CO 85374
866-392-5074 US Toll Free
123-456-3190 Cell
gpinfold@plavorix.com
The old tag line that we had on the business cars was.
Delivering Dependable Drawing and Document Tools to Design Teams Worldwide.
If you have an idea for a better tag line we are open to that also.
Updates
We would like to thank all of the Designers for their wonderful work. We apologize that we will not have the time to provide feedback to everyone. There is just so many innovative and professional designs that you have all created making our decision even harder.
Target Market(s)
Architects and Engineers
Industry/Entity Type
Business
Look and feel

```html
<!DOCTYPE html>
<html lang="en">
<head>
<meta charset="utf-8">
<title>Plavorix Business Card</title>
<link href="https://fonts.googleapis.com/css2?family=Arimo:wght@400;700&family=Open+Sans:wght@400&display=swap" rel="stylesheet">
<style>
  :root {
    --page: #e4e4e8;
    --card-white: #ffffff;
    --band-grey: #686868;
    --back-grey: #666666;
    --ink-grey: #5e5e5e;
    --accent-orange: #f0682a;
    --accent-red: #d8452b;
    --text-light: #ffffff;
  }
  * { box-sizing: border-box; margin: 0; padding: 0; }
  html, body { width: 1200px; height: 987px; overflow: hidden; }
  body {
    background: var(--page);
    font-family: "Arimo", Arial, sans-serif;
    position: relative;
  }
  .card {
    position: absolute;
    top: 333px;
    width: 560px;
    height: 320px;
    border-radius: 22px;
    overflow: hidden;
    box-shadow: 0 10px 26px rgba(0,0,0,0.18);
  }
  .card-front { left: 20px; background: var(--card-white); }
  .card-back { left: 620px; background: var(--back-grey); }

  /* front */
  .brand {
    position: absolute;
    left: 34px;
    top: 34px;
    display: flex;
    align-items: center;
    gap: 16px;
  }
  .brand-dot {
    width: 58px; height: 58px;
    border-radius: 50%;
    background: var(--accent-orange);
  }
  .brand-name {
    font-weight: 700;
    font-size: 66px;
    line-height: 1;
    letter-spacing: -2px;
    color: var(--ink-grey);
  }
  .rule {
    position: absolute;
    left: 0; right: 0;
    height: 2px;
  }
  .rule-top { top: 124px; background: var(--accent-red); }
  .rule-bottom { top: 252px; background: var(--accent-orange); }
  .contact-band {
    position: absolute;
    left: 0; right: 0;
    top: 130px;
    height: 116px;
    background: var(--band-grey);
    color: var(--text-light);
    display: flex;
    align-items: center;
    font-size: 17px;
    line-height: 1.3;
  }
  .address {
    width: 260px;
    text-align: right;
    padding-right: 16px;
    font-style: normal;
  }
  .divider {
    width: 2px;
    height: 78px;
    background: rgba(255,255,255,0.75);
  }
  .contact-list {
    list-style: none;
    padding-left: 16px;
  }
  .contact-list li {
    display: flex;
    align-items: center;
    gap: 8px;
  }
  .contact-list svg { width: 13px; height: 13px; flex: none; }
  .person {
    position: absolute;
    left: 30px;
    top: 266px;
    font-size: 22px;
    color: var(--ink-grey);
  }
  .person-name { color: var(--accent-orange); font-weight: 700; }

  /* back */
  .back-mark {
    position: absolute;
    left: 0; right: 0;
    top: 70px;
    display: flex;
    justify-content: center;
    align-items: center;
    gap: 14px;
  }
  .back-mark .brand-dot { width: 62px; height: 62px; }
  .back-mark .brand-name { color: var(--text-light); font-size: 58px; }
  .tagline {
    position: absolute;
    left: 40px; right: 40px;
    top: 196px;
    text-align: center;
    font-family: "Open Sans", Arial, sans-serif;
    font-size: 19px;
    line-height: 1.35;
    color: var(--text-light);
  }
</style>
</head>
<body>
  <section class="card card-front" aria-label="Business card front">
    <div class="brand">
      <span class="brand-dot"></span>
      <span class="brand-name">Plavorix</span>
    </div>
    <div class="rule rule-top"></div>
    <div class="contact-band">
      <address class="address">
        4738 W. Harrowgate Lane<br>
        STE 305<br>
        PMB#417, Larkmoor, CO 85374
      </address>
      <div class="divider"></div>
      <ul class="contact-list">
        <li>
          <svg viewBox="0 0 16 16" aria-hidden="true"><circle cx="8" cy="8" r="7" fill="none" stroke="#fff" stroke-width="1.5"/><path d="M5 4.5l2 2-1 1c.6 1.2 1.4 2 2.6 2.6l1-1 2 2-1.2 1.2C7.6 12 4 8.4 3.8 5.6z" fill="#fff"/></svg>
          866-392-5074(US) TF
        </li>
        <li>
          <svg viewBox="0 0 16 16" aria-hidden="true"><rect x="4" y="1" width="8" height="14" rx="1.5" fill="#fff"/><rect x="5.5" y="3" width="5" height="5" fill="#686868"/><circle cx="8" cy="12" r="1" fill="#686868"/></svg>
          123-456-3190
        </li>
        <li>
          <svg viewBox="0 0 16 16" aria-hidden="true"><rect x="1" y="3.5" width="14" height="9" rx="1" fill="#fff"/><path d="M1.5 4l6.5 5 6.5-5" fill="none" stroke="#686868" stroke-width="1.3"/></svg>
          gpinfold@plavorix.com
        </li>
      </ul>
    </div>
    <div class="rule rule-bottom"></div>
    <p class="person"><span class="person-name">Gerald Pinfold,</span> Vice President</p>
  </section>

  <section class="card card-back" aria-label="Business card back">
    <div class="back-mark">
      <span class="brand-dot"></span>
      <span class="brand-name">Plavorix</span>
    </div>
    <p class="tagline">Delivering Dependable Drawing and Document Tools<br>to Design Teams Worldwide</p>
  </section>
</body>
</html>
```